PowerPoint template design for TJMalverne Consulting

I'm interested in a PowerPoint template design that incorporates my logo (see attached file). I am an economist who mostly shows charts and tables in Calibri 24 point. Most tables are 4 or 5 columns by 14 or 15 rows so the design should seek to maximize work space on the slide while unmistakably indicating that these are my slides. I will be using the template design when I provide copies of my slides to the audience after the presentation, mostly in PDF format.

Target Market(s)

Mostly non-data types including educators.

Industry/Entity Type

Consulting

Font styles to use
Sans Serif

Colors
00a990
33b8a4
86cfc6

Requirements
Must have
• Looking for something more sleek and subtle, that doesn't take up too much screen real estate and that in some manner incorporates my business card/logo design. The logo doesn't have to be exactly incorporated as is, but it should visually align or mesh. I like the teal and gray/dark gray color palette that is on my business card.
Nice to have
• Open to more transparency/faded coloring, less bold and vivid than subtle background.
Should not have
• The goal is a PP template design that is unmistakably mine but is not so intrusive that it is the focus of every slide. I want the viewer to forget that the slide is coming from me as a consultant and focus on the content of the slide. I'm not using this as part of a marketing or advertising push as much as I am marking my material so folks who refer to the slides at a later date will know that they are mine.

```html
<!DOCTYPE html>
<html lang="en">
<head>
<meta charset="UTF-8">
<title>TJMalverne Consulting – Slide Template</title>
<link href="https://fonts.googleapis.com/css2?family=Open+Sans:wght@400;600;700&display=swap" rel="stylesheet">
<style>
  :root {
    --teal: #00a990;
    --teal-mid: #33b8a4;
    --teal-light: #86cfc6;
    --teal-wash: #e3f4f1;
    --ink: #3a3f44;
    --ink-soft: #6b7177;
    --stage: #e9eaeb;
    --paper: #ffffff;
    --placeholder: #dfe3e4;
  }
  * { box-sizing: border-box; margin: 0; padding: 0; }
  html, body { width: 849px; height: 1200px; overflow: hidden; }
  body {
    background: var(--stage);
    font-family: "Open Sans", sans-serif;
    color: var(--ink);
    position: relative;
  }
  .slide {
    position: absolute;
    left: 50px;
    width: 749px;
    height: 564px;
    background: var(--paper);
    box-shadow: 0 2px 6px rgba(0,0,0,.18);
    overflow: hidden;
  }
  .slide--services { top: 16px; }
  .slide--tables { top: 604px; }

  .slide__header { position: absolute; left: 30px; top: 14px; }
  .slide__tagline { font-size: 10px; font-weight: 600; letter-spacing: .3px; color: var(--ink); }
  .slide__date { font-size: 9px; color: var(--teal); margin-top: 2px; }
  .slide__rule { position: absolute; left: 30px; right: 30px; top: 44px; height: 2px; background: var(--teal); }
  .slide__title { position: absolute; left: 30px; top: 52px; font-size: 24px; font-weight: 700; color: var(--teal); letter-spacing: .5px; }

  .brand { position: absolute; right: 30px; bottom: 14px; display: flex; align-items: center; gap: 7px; }
  .brand__mark { width: 18px; height: 18px; background: var(--teal); }
  .brand__name { font-size: 12px; font-weight: 700; color: var(--ink); }

  /* services diagram */
  .services__lines { position: absolute; left: 0; top: 0; }
  .services__figure {
    position: absolute; left: 330px; top: 100px; width: 90px; height: 370px;
    background: linear-gradient(180deg, var(--teal) 0%, #0b8f7b 100%);
    border-radius: 40px 40px 6px 6px;
  }
  .step {
    position: absolute; width: 28px; height: 28px; border-radius: 50%;
    background: var(--teal); color: #fff; font-size: 14px; font-weight: 700;
    display: flex; align-items: center; justify-content: center;
  }
  .step-note { position: absolute; display: flex; gap: 8px; align-items: flex-start; }
  .step-note__icon { width: 30px; height: 30px; background: var(--placeholder); border-radius: 4px; flex: none; }
  .step-note__text { font-size: 8.5px; line-height: 1.35; color: var(--ink); width: 82px; }
  .step-note__text li { list-style: none; padding-left: 8px; position: relative; }
  .step-note__text li::before { content: "•"; position: absolute; left: 0; color: var(--teal); }

  /* data table */
  .data-table {
    position: absolute; left: 90px; top: 92px; width: 580px;
    border-collapse: collapse; font-size: 9.5px;
  }
  .data-table th {
    background: var(--teal); color: #fff; font-weight: 600; height: 24px;
    border-left: 1px solid #fff;
  }
  .data-table th:first-child { background: transparent; border: none; }
  .data-table td { height: 24.3px; text-align: center; border-left: 1px solid #fff; border-bottom: 1px solid #fff; }
  .data-table td.region { text-align: right; padding-right: 10px; background: var(--paper); border: none; }
  .data-table tbody tr:nth-child(odd) td:not(.region) { background: var(--teal-wash); }
  .data-table tbody tr:nth-child(even) td:not(.region) { background: #c9ebe5; }
</style>
</head>
<body>

<section class="slide slide--services">
  <header class="slide__header">
    <p class="slide__tagline">LABOR MARKET ECONOMIST AND SPEAKER PAR EXCELLENCE</p>
    <p class="slide__date">July 2015</p>
  </header>
  <div class="slide__rule"></div>
  <h1 class="slide__title">OUR SERVICES</h1>

  <svg class="services__lines" width="749" height="564" aria-hidden="true">
    <g fill="none" stroke="var(--ink)" stroke-width="2" stroke-dasharray="6 5">
      <path d="M274 106 H62 V255"/>
      <path d="M62 283 V377"/>
      <path d="M68 405 V470 H679 V433"/>
      <path d="M679 405 V306"/>
      <path d="M685 278 V106 H492"/>
    </g>
  </svg>

  <div class="services__figure" role="img" aria-label="Illustration of a consultant in a suit"></div>

  <div class="step" style="left:274px;top:92px">1</div>
  <div class="step" style="left:48px;top:255px">2</div>
  <div class="step" style="left:54px;top:377px">3</div>
  <div class="step" style="left:665px;top:405px">4</div>
  <div class="step" style="left:671px;top:278px">5</div>
  <div class="step" style="left:464px;top:92px">6</div>

  <div class="step-note" style="left:250px;top:130px">
    <ul class="step-note__text"><li>The Southeast Center was established in 1991 as one of a select number of</li></ul>
  </div>
  <div class="step-note" style="left:90px;top:215px">
    <div class="step-note__icon" role="img" aria-label="Headset icon"></div>
    <ul class="step-note__text"><li>The Southeast Center was established in 1991 as one of a select number of</li></ul>
  </div>
  <div class="step-note" style="left:96px;top:340px">
    <div class="step-note__icon" role="img" aria-label="Group of people icon"></div>
    <ul class="step-note__text"><li>The Southeast Center was established in 1991 as one of a select number of</li></ul>
  </div>
  <div class="step-note" style="left:440px;top:130px">
    <ul class="step-note__text"><li>The Southeast Center was established in 1991 as one of a select number of</li></ul>
  </div>
  <div class="step-note" style="left:470px;top:235px">
    <ul class="step-note__text"><li>The Southeast Center was established in 1991 as one of a select number of</li></ul>
    <div class="step-note__icon" role="img" aria-label="Rising chart icon"></div>
  </div>
  <div class="step-note" style="left:470px;top:370px">
    <div class="step-note__icon" role="img" aria-label="Presenter at board icon"></div>
    <ul class="step-note__text"><li>The Southeast Center was established in 1991 as one of a select number of</li></ul>
  </div>

  <div class="brand"><span class="brand__mark"></span><span class="brand__name">TJMalverne Consulting</span></div>
</section>

<section class="slide slide--tables">
  <header class="slide__header">
    <p class="slide__tagline">LABOR MARKET ECONOMIST AND SPEAKER PAR EXCELLENCE</p>
    <p class="slide__date">July 2015</p>
  </header>
  <div class="slide__rule"></div>
  <h1 class="slide__title">OUR TABLES</h1>

  <table class="data-table">
    <thead>
      <tr><th></th><th>2002-2004</th><th>2005-2007</th><th>2008-2010</th><th>2011-2013</th><th>2014-2016</th></tr>
    </thead>
    <tbody>
      <tr><td class="region">North America</td><td>9.6</td><td>15.6</td><td>3.5</td><td>15.6</td><td>3.5</td></tr>
      <tr><td class="region">Latin America</td><td>11.4</td><td>11.1</td><td>9.6</td><td>11.1</td><td>9.6</td></tr>
      <tr><td class="region">Western Europe</td><td>9.5</td><td>5.2</td><td>5.5</td><td>5.2</td><td>5.5</td></tr>
      <tr><td class="region">Eastern Europe</td><td>14.6</td><td>17.2</td><td>10.7</td><td>17.2</td><td>10.7</td></tr>
      <tr><td class="region">Japan</td><td>2.8</td><td>4.8</td><td>1.2</td><td>4.8</td><td>1.2</td></tr>
      <tr><td class="region">Asia-Pacific (ex-Japan)</td><td>18.2</td><td>30.5</td><td>15.8</td><td>30.5</td><td>15.8</td></tr>
      <tr><td class="region">Middle East and Africa</td><td>8.6</td><td>11.6</td><td>6.6</td><td>11.6</td><td>6.6</td></tr>
      <tr><td class="region">Global</td><td>8.7</td><td>14.6</td><td>5.4</td><td>14.6</td><td>5.4</td></tr>
      <tr><td class="region">North America</td><td>9.6</td><td>15.6</td><td>3.5</td><td>15.6</td><td>3.5</td></tr>
      <tr><td class="region">Latin America</td><td>11.4</td><td>11.1</td><td>9.6</td><td>11.1</td><td>9.6</td></tr>
      <tr><td class="region">Western Europe</td><td>9.5</td><td>5.2</td><td>5.5</td><td>5.2</td><td>5.5</td></tr>
      <tr><td class="region">Eastern Europe</td><td>14.6</td><td>17.2</td><td>10.7</td><td>17.2</td><td>10.7</td></tr>
      <tr><td class="region">Japan</td><td>2.8</td><td>4.8</td><td>1.2</td><td>4.8</td><td>1.2</td></tr>
      <tr><td class="region">Asia-Pacific (ex-Japan)</td><td>18.2</td><td>30.5</td><td>15.8</td><td>30.5</td><td>15.8</td></tr>
      <tr><td class="region">Middle East and Africa</td><td>8.6</td><td>11.6</td><td>6.6</td><td>11.6</td><td>6.6</td></tr>
      <tr><td class="region">Global</td><td>8.7</td><td>14.6</td><td>5.4</td><td>14.6</td><td>5.4</td></tr>
    </tbody>
  </table>

  <div class="brand"><span class="brand__mark"></span><span class="brand__name">TJMalverne Consulting</span></div>
</section>

</body>
</html>
```